Need Help having my business card stand out

I am the owner of Birchway Canine Training and would like for my business cards to stand out. I have been trying to keep designing them myself but I can't get what I have in my head on the card. I will try my best to post templates that I like for inspirations. I want something unique but elegant. I don't want in to look cartoony or cheesy. It needs to pop in a pet shop but also in a coffee shop or gym.

Target Market(s)

Dog owners, Married ,No young kids Jr High school kids and up (maybe kids on the way) Executives, Stay at home moms/wives, Small business owners

Industry/Entity Type

Dog Training

Contact Information for Business Card

Lowell Spratt, 281-904-3376, info@birchwaycanine.example, www.birchwaycanine.example

Colors

Designer to choose colors to be used in the design.

Requirements
Must have
• my logo
Should not have
• Cursive lettering

```html
<!DOCTYPE html>
<html lang="en">
<head>
<meta charset="utf-8">
<title>Birchway Canine Training – Business Card</title>
<link rel="stylesheet" href="https://fonts.googleapis.com/css2?family=Roboto+Condensed:wght@400;700&family=Roboto:wght@400;700&display=swap">
<style>
  :root {
    --page: #ffffff;
    --orange: #f5822a;
    --panel-dark: #262626;
    --panel-mid: #474747;
    --text-light: #ffffff;
    --text-dark: #1c1c1c;
    --photo-warm: #d9c3a3;
    --photo-green: #9aa57e;
    --photo-red: #b9524c;
  }
  html, body {
    margin: 0;
    padding: 0;
    width: 1200px;
    height: 707px;
    overflow: hidden;
    background: var(--page);
  }
  .card {
    position: relative;
    width: 1200px;
    height: 707px;
    background: var(--page);
    font-family: "Roboto Condensed", "Arial Narrow", sans-serif;
  }
  .portrait {
    position: absolute;
    left: 4px;
    top: 20px;
    width: 460px;
    height: 675px;
    border-radius: 40px 0 0 40px;
    background:
      radial-gradient(ellipse 45% 40% at 35% 40%, var(--photo-red) 0%, rgba(185,82,76,0) 100%),
      radial-gradient(ellipse 40% 30% at 60% 78%, #b8946a 0%, rgba(184,148,106,0) 100%),
      linear-gradient(180deg, #e8dccb 0%, var(--photo-warm) 45%, var(--photo-green) 100%);
  }
  .divider-vertical {
    position: absolute;
    left: 466px;
    top: 20px;
    width: 6px;
    height: 685px;
    background: var(--orange);
  }
  .panel {
    position: absolute;
    left: 485px;
    top: 20px;
    width: 709px;
    height: 678px;
    border-radius: 0 58px 58px 0;
    background: radial-gradient(ellipse 70% 60% at 55% 45%, var(--panel-mid) 0%, var(--panel-dark) 100%);
    overflow: hidden;
  }
  .logo-banner {
    position: absolute;
    left: 231px;
    top: 0;
    width: 264px;
    height: 184px;
  }
  .logo-name {
    position: absolute;
    left: 0;
    top: 56px;
    width: 264px;
    text-align: center;
    font-weight: 700;
    font-size: 34px;
    letter-spacing: 1px;
    color: var(--text-dark);
  }
  .identity {
    position: absolute;
    left: 52px;
    top: 322px;
    display: flex;
    align-items: baseline;
    gap: 10px;
  }
  .identity .name {
    font-weight: 700;
    font-size: 40px;
    color: var(--orange);
    text-transform: uppercase;
    letter-spacing: 0.3px;
  }
  .identity .role {
    font-weight: 700;
    font-size: 23px;
    color: var(--text-light);
  }
  .divider-horizontal {
    position: absolute;
    left: 45px;
    top: 391px;
    width: 664px;
    height: 4px;
    background: var(--orange);
  }
  .contacts {
    position: absolute;
    top: 492px;
    display: flex;
    flex-direction: column;
    gap: 14px;
  }
  .contacts.left { left: 52px; }
  .contacts.right { left: 364px; }
  .contact {
    display: flex;
    align-items: center;
    gap: 17px;
    height: 26px;
    font-size: 21px;
    color: var(--text-light);
    white-space: nowrap;
  }
  .icon {
    width: 26px;
    height: 26px;
    flex: none;
  }
</style>
</head>
<body>
<div class="card">
  <div class="portrait" role="img" aria-label="Photo of the trainer kneeling on grass outdoors beside a shepherd dog"></div>
  <div class="divider-vertical"></div>

  <div class="panel">
    <div class="logo-banner">
      <svg width="264" height="184" viewBox="0 0 264 184">
        <polygon points="0,0 22,0 22,150 0,150" fill="var(--orange)"/>
        <polygon points="242,0 264,0 264,150 242,150" fill="var(--orange)"/>
        <polygon points="20,0 244,0 244,184 132,150 20,184" fill="#ffffff"/>
      </svg>
      <div class="logo-name">Birchway</div>
    </div>

    <div class="identity">
      <span class="name">Lowell Spratt</span>
      <span class="role">Head(Birchway)</span>
    </div>
    <div class="divider-horizontal"></div>

    <div class="contacts left">
      <div class="contact">
        <svg class="icon" viewBox="0 0 26 26"><circle cx="13" cy="13" r="13" fill="var(--orange)"/><path d="M9.2 7.5c.6-.4 1.2-.2 1.5.3l1 1.7c.3.5.1 1-.3 1.3l-.6.5c.5 1.3 1.6 2.5 2.9 3.1l.5-.6c.4-.4.9-.5 1.3-.2l1.7 1c.5.3.7.9.3 1.5-.7 1-1.7 1.6-2.8 1.2-2.9-1-5.1-3.3-6.1-6.1-.4-1.1.2-2.1 1.2-2.7z" fill="#fff"/></svg>
        <span>281-904-3376</span>
      </div>
      <div class="contact">
        <svg class="icon" viewBox="0 0 26 26"><circle cx="13" cy="13" r="13" fill="var(--orange)"/></svg>
        <span>birchwaycanine</span>
      </div>
      <div class="contact">
        <svg class="icon" viewBox="0 0 26 26"><circle cx="13" cy="13" r="13" fill="var(--orange)"/><rect x="7.5" y="9" width="11" height="8" rx="1" fill="#fff"/><path d="M7.8 9.4 13 13.3l5.2-3.9" fill="none" stroke="var(--orange)" stroke-width="1.2"/></svg>
        <span>info@birchwaycanine.example</span>
      </div>
    </div>

    <div class="contacts right">
      <div class="contact">
        <svg class="icon" viewBox="0 0 26 26"><circle cx="13" cy="13" r="13" fill="var(--orange)"/></svg>
        <span>Birchway Canine Training</span>
      </div>
      <div class="contact">
        <svg class="icon" viewBox="0 0 26 26"><circle cx="13" cy="13" r="13" fill="var(--orange)"/><circle cx="13" cy="13" r="5.5" fill="none" stroke="#fff" stroke-width="1.4"/><path d="M7.5 13h11M13 7.5c-2.2 2.8-2.2 8.2 0 11M13 7.5c2.2 2.8 2.2 8.2 0 11" fill="none" stroke="#fff" stroke-width="1.1"/></svg>
        <span>www.birchwaycanine.example</span>
      </div>
      <div class="contact">
        <svg class="icon" viewBox="0 0 26 26"><circle cx="13" cy="13" r="13" fill="var(--orange)"/></svg>
        <span>Birchway Canine Training</span>
      </div>
    </div>
  </div>
</div>
</body>
</html>
```